Stage Design Company Business Card

We are looking to step up up our business card design for our team.

We are a Full service Design and Consultation company for Stage and TV with an emphasis in Theatrical Lighting.

We like our materials to be clean and modern with solid colors free of patterns and gradients. Our brand consists of 4 primary colors Purple, Black, Grey, and White. Provided is our Word Mark as well as our Symbol Logo.

We would like our cards to leave an impression beyond the information, show our attention to design and detail, and make our marks an easily recognized feature (together or apart) for our clients.

We need a warm approachable comfortable feel for some clients, and a professional flair for the board member type clients.

Attached are our brand elements, and our existing cards to give a sense of our style and a glipse at the information we provide on our cards.

Target Market(s)

broad client base from church leaders to high school teachers and architects.

Industry/Entity Type

Business

Contact Information for Business Card

We format our phone number with periods not parenthesis or dashes. Information will be edited for each of our team members, and team member specific cards are not part of this scope, but rather a template so to speak.

Font styles to use
Sans Serif

Colors
6b449b
ffffff
000000
333333
aaaaaa

Requirements
Must have
• Wordmark and logo mark present (does not need to exist on the same side of card)
• Brand Colors,
• Name, Phone, Email, Address.
• Unique choices that make someone stop and take a second look
Nice to have
• It would be nice to somehow convey what we DO, as our brand name does not lend itself to this, outside of an obvious tagline though.....
• social media if not crowded. all of our handles match (instagram, twitter, facebook)
Should not have
• "clipart"

```html
<!DOCTYPE html>
<html lang="en">
<head>
<meta charset="utf-8">
<title>Halvern Business Card</title>
<link rel="stylesheet" href="https://fonts.googleapis.com/css2?family=Open+Sans:wght@400;600&display=swap">
<style>
  :root {
    --backdrop: #e9e7e4;
    --card: #333333;
    --purple: #6b449b;
    --ink: #ffffff;
    --ink-soft: #e6e6e6;
    --grey: #aaaaaa;
  }
  * { margin: 0; padding: 0; box-sizing: border-box; }
  html, body {
    width: 1200px;
    height: 899px;
    overflow: hidden;
    background: var(--backdrop);
    font-family: "Open Sans", sans-serif;
    color: var(--ink);
  }
  .card {
    position: absolute;
    width: 554px;
    height: 341px;
    background: var(--card);
    box-shadow: 0 6px 18px rgba(0,0,0,0.18);
  }
  .card-front { left: 239px; top: 61px; }
  .card-back  { left: 458px; top: 518px; }

  .front-brand {
    position: absolute;
    left: 56px;
    top: 150px;
    width: 200px;
    display: flex;
    align-items: center;
    justify-content: center;
    gap: 12px;
  }
  .front-dot {
    width: 18px;
    height: 18px;
    border-radius: 50%;
    background: var(--purple);
  }
  .front-name {
    font-size: 24px;
    font-weight: 600;
    letter-spacing: 3px;
  }
  .front-divider {
    position: absolute;
    left: 258px;
    top: 80px;
    width: 2px;
    height: 180px;
    background: var(--purple);
  }
  .details {
    position: absolute;
    left: 300px;
    top: 76px;
  }
  .person-name {
    font-size: 22px;
    font-weight: 400;
    line-height: 1.2;
  }
  .person-role {
    font-size: 14.5px;
    color: var(--grey);
    line-height: 1.3;
  }
  .address {
    margin-top: 16px;
    font-size: 14.5px;
    line-height: 1.38;
    color: var(--ink-soft);
  }
  .contacts {
    list-style: none;
    margin-top: 14px;
    font-size: 14.5px;
    line-height: 1.38;
    color: var(--ink-soft);
  }
  .contacts li { display: flex; align-items: center; gap: 8px; }
  .contacts svg { width: 12px; height: 12px; fill: var(--purple); flex: none; }

  .back-accent {
    position: absolute;
    left: 0; right: 0; bottom: 0;
    height: 8px;
    background: var(--purple);
  }
  .back-brand {
    position: absolute;
    left: 0; right: 0;
    top: 148px;
    display: flex;
    align-items: center;
    justify-content: center;
    gap: 22px;
  }
  .brand-dot {
    width: 44px;
    height: 44px;
    border-radius: 50%;
    background: var(--purple);
  }
  .brand-name {
    font-size: 34px;
    font-weight: 600;
    letter-spacing: 14px;
  }
</style>
</head>
<body>
  <section class="card card-front">
    <div class="front-brand">
      <span class="front-dot"></span>
      <span class="front-name">HALVERN</span>
    </div>
    <div class="front-divider"></div>
    <div class="details">
      <p class="person-name">Marcus Hale</p>
      <p class="person-role">Managing Director</p>
      <p class="address">2780, Lantern Row Avenue<br>Westfield County, 482910.</p>
      <ul class="contacts">
        <li>
          <svg viewBox="0 0 24 24" aria-hidden="true"><path d="M6.6 10.8a15.2 15.2 0 0 0 6.6 6.6l2.2-2.2a1 1 0 0 1 1-.25 11.4 11.4 0 0 0 3.6.57 1 1 0 0 1 1 1V20a1 1 0 0 1-1 1A17 17 0 0 1 3 4a1 1 0 0 1 1-1h3.5a1 1 0 0 1 1 1c0 1.25.2 2.45.57 3.57a1 1 0 0 1-.25 1z"/></svg>
          044.987.654.321
        </li>
        <li>
          <svg viewBox="0 0 24 24" aria-hidden="true"><path d="M2 7.5V19h20V7.5l-10 7z M2.5 5h19L12 12z"/></svg>
          hello@halvern.com
        </li>
        <li>
          <svg viewBox="0 0 24 24" aria-hidden="true"><path d="M10.6 13.4a1 1 0 0 1 0-1.4l3.5-3.5a1 1 0 1 1 1.4 1.4L12 13.4a1 1 0 0 1-1.4 0z M8.5 20.5a5 5 0 0 1-3.5-8.5l2.1-2.1 1.4 1.4-2.1 2.1a3 3 0 0 0 4.2 4.2l2.1-2.1 1.4 1.4-2.1 2.1a5 5 0 0 1-3.5 1.5z M16.9 14.1l-1.4-1.4 2.1-2.1a3 3 0 0 0-4.2-4.2l-2.1 2.1-1.4-1.4L12 5a5 5 0 0 1 7 7z"/></svg>
          www.halvern.com
        </li>
      </ul>
    </div>
  </section>

  <section class="card card-back">
    <div class="back-brand">
      <span class="brand-dot"></span>
      <span class="brand-name">HALVERN</span>
    </div>
    <div class="back-accent"></div>
  </section>
</body>
</html>
```